Creative Brief
Pelmora Wealth Partners Brochure
Brochure Design 2011
Your Horizons Built Freely
We need a tri-fold brochure for our company Pelmora Wealth Partners. We already have a custom logo created and need that inserted into the brochure. We are a independent financial services company, we offer investment advice and products to consumers and business.
Financial Services
Consumers & Business
Must use our current company logo,you can get it here:
https://photovault-example.net/MarcusOlvey/PelmoraWealthPartners?authkey=Xq7tLmBVNrrKdT2WzaHJ&feat=directlink
Also need all content including sections to be editable. Need at least three sections (Example: "The Company", "Our Services", etc...)
Pelmora Wealth Partners Logo
Logo AI file
Logo AI File 2.0
Old Brochure Cover (Brightway Office)
old brochure Inner (Brightway Office)
This is a brochure which I like the style, simple and clean
Another Brochure in which I like
by far my favorite one, hope this inspires some ideas
more ideas

```html
<!DOCTYPE html>
<html lang="en">
<head>
<meta charset="utf-8">
<title>Pelmora Wealth Partners Tri-fold Brochure</title>
<link rel="stylesheet" href="https://fonts.googleapis.com/css2?family=Cormorant+Garamond:wght@500;600&family=Open+Sans:wght@400;600;700&display=swap">
<style>
  :root {
    --backdrop: #e9e6e1;
    --paper: #ffffff;
    --slate: #5f6d79;
    --slate-light: #a9b3bb;
    --green: #8cab3c;
    --green-light: #c5d88f;
    --text: #4a4f55;
    --muted: #8a9096;
    --box: #eef0f1;
    --photo-a: #b9c2c8;
    --photo-b: #d8cbb8;
  }
  * { box-sizing: border-box; margin: 0; padding: 0; }
  html, body { width: 1200px; height: 468px; overflow: hidden; }
  body {
    background: var(--backdrop);
    font-family: "Open Sans", sans-serif;
    color: var(--text);
    position: relative;
  }
  .spread {
    position: absolute;
    top: 84px;
    width: 540px;
    height: 300px;
    background: var(--paper);
    box-shadow: 0 4px 14px rgba(0,0,0,.18);
    overflow: hidden;
  }
  .spread--outside { left: 30px; }
  .spread--inside { left: 630px; }
  .spread__frame { position: absolute; inset: 0; width: 100%; height: 100%; }
  .panel {
    position: absolute;
    top: 0;
    width: 180px;
    height: 300px;
    padding: 34px 14px 0;
  }
  .panel--1 { left: 0; }
  .panel--2 { left: 180px; }
  .panel--3 { left: 360px; }

  .headline {
    font-size: 8px;
    font-weight: 700;
    color: var(--green);
    text-transform: uppercase;
    letter-spacing: .4px;
    line-height: 1.35;
  }
  .copy { font-size: 5px; line-height: 1.5; color: var(--text); margin-top: 5px; }
  .photo {
    background: linear-gradient(135deg, var(--photo-a), var(--photo-b));
    border: 1px solid #d4d7da;
  }

  /* outside */
  .solutions .headline { margin-top: 70px; }
  .solutions .photo { width: 120px; height: 54px; margin-top: 6px; }
  .solutions .copy { width: 120px; }
  .back-panel { text-align: center; }
  .back-panel .copy { color: var(--muted); margin-top: 18px; }
  .brand {
    display: inline-flex; align-items: center; gap: 4px;
    font-family: "Open Sans", sans-serif; font-weight: 700;
    color: var(--slate); letter-spacing: 1px;
  }
  .brand__mark { display: inline-block; background: var(--green); }
  .back-panel .brand { margin-top: 40px; font-size: 18px; }
  .back-panel .brand__mark { width: 14px; height: 14px; }
  .back-icons { display: flex; justify-content: center; gap: 8px; margin-top: 52px; }
  .back-icons span { width: 7px; height: 7px; background: var(--slate-light); display: block; }

  .cover .copy { text-align: center; color: var(--muted); margin-top: 0; }
  .cover__title {
    font-family: "Cormorant Garamond", serif;
    font-weight: 600;
    text-transform: uppercase;
    line-height: .95;
    margin-top: 46px;
    padding-left: 20px;
  }
  .cover__title .lead { display: block; font-size: 34px; color: var(--green); }
  .cover__title .rest { display: block; font-size: 15px; color: var(--slate); letter-spacing: 1px; margin-top: 3px; }
  .cover .brand { position: absolute; right: 14px; bottom: 26px; font-size: 8px; }
  .cover .brand__mark { width: 7px; height: 7px; }

  /* inside */
  .section-title {
    display: flex; align-items: center; gap: 4px;
    font-size: 6.5px; font-weight: 700; color: var(--slate);
    text-transform: uppercase; letter-spacing: .5px; margin-top: 12px;
  }
  .section-title::before { content: ""; width: 4px; height: 4px; background: var(--green); border-radius: 50%; }
  .section-title:first-child { margin-top: 0; }
  .vision-item { display: flex; gap: 6px; margin-top: 10px; }
  .vision-item .photo { flex: 0 0 32px; height: 24px; }
  .vision-item .copy { margin-top: 0; }
  .offer {
    display: flex; gap: 6px; background: var(--box);
    padding: 6px; margin-bottom: 10px; border-left: 2px solid var(--green);
  }
  .offer .photo { flex: 0 0 38px; height: 30px; }
  .offer__name { font-size: 6.5px; font-weight: 700; color: var(--green); }
  .offer .copy { margin-top: 2px; }
</style>
</head>
<body>

<section class="spread spread--outside" aria-label="Brochure outside">
  <svg class="spread__frame" viewBox="0 0 540 300" preserveAspectRatio="none" aria-hidden="true">
    <path d="M0 0H540V16C420 30 250 8 0 24Z" fill="var(--slate)"/>
    <path d="M0 276C160 252 360 300 540 262V300H0Z" fill="var(--slate-light)"/>
    <path d="M0 270C170 246 360 294 540 256" fill="none" stroke="var(--green)" stroke-width="3"/>
    <path d="M0 264C170 240 360 288 540 250" fill="none" stroke="var(--green-light)" stroke-width="1.2"/>
    <line x1="180" y1="24" x2="180" y2="260" stroke="#eceeef"/>
    <line x1="360" y1="24" x2="360" y2="260" stroke="#eceeef"/>
  </svg>

  <div class="panel panel--1 solutions">
    <h2 class="headline">Flexible solutions for<br>your business needs</h2>
    <div class="photo" role="img" aria-label="Photo of a business handshake"></div>
    <p class="copy">PLMR offers tailored financial guidance for firms and families seeking growth and security.</p>
  </div>

  <div class="panel panel--2 back-panel">
    <p class="copy">Pelmora Wealth Partners<br>Independent Financial Advisors</p>
    <div class="brand"><span class="brand__mark"></span>PLMR</div>
    <div class="back-icons" aria-hidden="true"><span></span><span></span><span></span></div>
  </div>

  <div class="panel panel--3 cover">
    <p class="copy">Pelmora Wealth Partners<br>Independent Financial Services</p>
    <h1 class="cover__title">
      <span class="lead">Your</span>
      <span class="rest">Horizons<br>Built Freely</span>
    </h1>
    <div class="brand"><span class="brand__mark"></span>PLMR</div>
  </div>
</section>

<section class="spread spread--inside" aria-label="Brochure inside">
  <svg class="spread__frame" viewBox="0 0 540 300" preserveAspectRatio="none" aria-hidden="true">
    <path d="M0 0H540V16C420 30 250 8 0 24Z" fill="var(--slate)"/>
    <path d="M0 276C160 252 360 300 540 262V300H0Z" fill="var(--slate-light)"/>
    <path d="M0 270C170 246 360 294 540 256" fill="none" stroke="var(--green)" stroke-width="3"/>
    <path d="M0 264C170 240 360 288 540 250" fill="none" stroke="var(--green-light)" stroke-width="1.2"/>
    <line x1="180" y1="24" x2="180" y2="260" stroke="#eceeef"/>
    <line x1="360" y1="24" x2="360" y2="260" stroke="#eceeef"/>
  </svg>

  <div class="panel panel--1">
    <h3 class="section-title">The Company</h3>
    <p class="copy">Pelmora Wealth Partners is an independent firm offering investment advice and products to consumers and businesses alike.</p>
    <p class="copy">We listen first, then build plans that fit your goals.</p>
    <h3 class="section-title">Our Services</h3>
    <p class="copy">Retirement planning, portfolio management, insurance and estate strategies for every stage of life.</p>
  </div>

  <div class="panel panel--2">
    <h3 class="section-title">Our Vision</h3>
    <div class="vision-item">
      <div class="photo" role="img" aria-label="Photo of an advisor meeting"></div>
      <p class="copy">Clear advice, honest fees and long term partnerships.</p>
    </div>
    <div class="vision-item">
      <div class="photo" role="img" aria-label="Photo of a planning session"></div>
      <p class="copy">Our advisors work for you, never for a product.</p>
    </div>
    <div class="vision-item">
      <div class="photo" role="img" aria-label="Photo of a family at home"></div>
      <p class="copy">Trusted by families and owners across the region.</p>
    </div>
  </div>

  <div class="panel panel--3">
    <div class="offer">
      <div class="photo" role="img" aria-label="Photo of financial documents"></div>
      <div><p class="offer__name">Wealth Planning</p><p class="copy">Goals mapped into a plan you can follow.</p></div>
    </div>
    <div class="offer">
      <div class="photo" role="img" aria-label="Photo of an office team"></div>
      <div><p class="offer__name">Business Services</p><p class="copy">Benefits, payroll plans and succession support.</p></div>
    </div>
    <div class="offer">
      <div class="photo" role="img" aria-label="Photo of a retired couple"></div>
      <div><p class="offer__name">Retirement</p><p class="copy">Income strategies built to last.</p></div>
    </div>
  </div>
</section>

</body>
</html>
```